Business Card Design Project

This is the first time we use our new logo. We need a business card that we can use both on our institutional corporate relationships and also that works for our staff that deals with consumers directly.

VELUNDA is a new company dedicated to empower consumers and to provide them with the best choices for specialized health care using the latest telemedicine technology (medicine at a distance via videoconference).

We want to print this cards in high quality materials and process. We will like designs that allow us to use UV spot varnish and other techniques that will differentiate us.

We are including Two different versions of Color logos. In addition we are including white over black background logos. Those can be used replacing the black for a color.

Please note this is the first time we will be creating any corporate materials with our new logo and colors.

Target Market(s)

34+ consumers of medium high and high socioeconomic levels.

Industry/Entity Type

Health

Requirements
Must have
• Our logo on its original colors
Should not have
• Any other graphical element or design that is not our logo

```html
<!DOCTYPE html>
<html lang="en">
<head>
<meta charset="utf-8">
<title>VELUNDA Business Card</title>
<link rel="stylesheet" href="https://fonts.googleapis.com/css2?family=Mulish:wght@400;800&family=Arimo:wght@400&display=swap">
<style>
  :root {
    --bg: #e4e5e9;
    --card: #ffffff;
    --navy: #1d5b86;
    --teal: #1aa79a;
    --sky: #5bb6df;
    --ink: #2a2a2a;
    --rule: #c9c9cc;
  }
  * { margin: 0; padding: 0; box-sizing: border-box; }
  html, body { width: 1200px; height: 987px; overflow: hidden; }
  body {
    background: var(--bg);
    position: relative;
    font-family: "Mulish", sans-serif;
  }
  .card {
    position: absolute;
    width: 620px;
    height: 360px;
    background: var(--card);
    border-radius: 32px;
    box-shadow: 0 10px 24px rgba(0,0,0,0.12);
  }
  .card--back { left: 520px; top: 90px; }
  .card--front { left: 60px; top: 540px; }

  .brand {
    display: flex;
    align-items: center;
    gap: 16px;
    color: var(--navy);
    font-family: "Mulish", sans-serif;
    font-weight: 800;
    letter-spacing: 4px;
  }
  .brand__dot {
    width: 44px; height: 44px;
    border-radius: 50%;
    background: var(--teal);
    flex: none;
  }

  .card--back .brand {
    position: absolute;
    left: 0; right: 0; top: 120px;
    justify-content: center;
    font-size: 60px;
  }
  .card--back .web {
    position: absolute;
    left: 0; right: 0; top: 215px;
    text-align: center;
    font-family: "Arimo", sans-serif;
    font-size: 22px;
    letter-spacing: 6px;
    color: var(--ink);
  }
  .card--back .web strong { color: var(--navy); font-weight: 400; }

  .card--front .brand {
    position: absolute;
    left: 50px; top: 48px;
    font-size: 52px;
  }
  .card--front .rule {
    position: absolute;
    left: 50px; right: 50px; top: 140px;
    height: 2px;
    background: var(--rule);
  }
  .person {
    position: absolute;
    left: 0; right: 0; top: 168px;
    text-align: center;
    font-size: 26px;
    font-weight: 800;
    color: var(--navy);
  }
  .person span { font-weight: 400; color: var(--teal); }
  .contact {
    position: absolute;
    left: 50px; right: 50px; top: 222px;
    font-family: "Arimo", sans-serif;
    font-size: 19px;
    color: var(--ink);
    line-height: 1.75;
    text-align: center;
  }
  .contact .row { display: flex; justify-content: center; gap: 26px; }
  .contact .item { display: inline-flex; align-items: center; gap: 7px; }
  .contact svg { width: 16px; height: 16px; flex: none; }
</style>
</head>
<body>

  <section class="card card--back">
    <div class="brand"><span class="brand__dot"></span>VELUNDA</div>
    <p class="web">www.<strong>velunda</strong>.com</p>
  </section>

  <section class="card card--front">
    <div class="brand"><span class="brand__dot"></span>VELUNDA</div>
    <div class="rule"></div>
    <p class="person">Your Name, <span>Title</span></p>
    <div class="contact">
      <div class="row">
        <span class="item">
          <svg viewBox="0 0 16 16"><circle cx="8" cy="8" r="7.5" fill="var(--navy)"/><path d="M5 4.5c0 3.5 3 6.5 6.5 6.5l.5-1.6-1.8-.9-.8.8c-1-.5-1.9-1.4-2.4-2.4l.8-.8-.9-1.8z" fill="#fff"/></svg>
          012-555-0189
        </span>
        <span class="item">
          <svg viewBox="0 0 16 16"><circle cx="8" cy="8" r="7.5" fill="var(--navy)"/><path d="M5 4.5c0 3.5 3 6.5 6.5 6.5l.5-1.6-1.8-.9-.8.8c-1-.5-1.9-1.4-2.4-2.4l.8-.8-.9-1.8z" fill="#fff"/></svg>
          012-555-0189
        </span>
      </div>
      <div class="row">
        <span class="item">
          <svg viewBox="0 0 16 16"><rect x="1" y="3.5" width="14" height="9" rx="1" fill="var(--navy)"/><path d="M1.5 4l6.5 5 6.5-5" stroke="#fff" stroke-width="1.2" fill="none"/></svg>
          name@velunda.com
        </span>
        <span class="item">
          <svg viewBox="0 0 16 16"><circle cx="8" cy="8" r="7" fill="none" stroke="var(--navy)" stroke-width="1.4"/><ellipse cx="8" cy="8" rx="3" ry="7" fill="none" stroke="var(--navy)" stroke-width="1.2"/><path d="M1 8h14" stroke="var(--navy)" stroke-width="1.2"/></svg>
          www.velunda.com
        </span>
      </div>
      <div class="row">
        <span class="item">Street Name, City Name, State, City Zip Code</span>
      </div>
    </div>
  </section>

</body>
</html>
```